Business card design for a dynamic IT consulting company

We need a business card design for a young firm, specialized in the Telecommunications/Consulting industry. The name of the company is Quindor and Partners Business Consulting Ltd. (Short name: Quindor and Partnes)
Quindor = solve read reverse, so we aim to be uncomplicated and solution-oriented. The small pipe in our logo is also related to the word solve. So we need a new business card design, which is simple, eye catching and something non traditional (I would probably prefer a square shaped design rather than a rectangle, but open for suggestions). Attached our logo.

Target Market(s)

Usually our customers are Tier1 Telecoms providers (Q-Netra, Palorix, etc) and their executives.

Industry/Entity Type

Business

Contact Information for Business Card

Name: Bence Tolnavari
Email: b.tolnavari@quindor.hu
Web: www.quindor.hu
Mobile: +36 30 518 2769
Title: Managing Director

Optional:
Company name: Quindor and Partners Ltd.
Address: 1087 Budapest, Tolvenka str. 28/C, Hungary

Font styles to use
Other font styles liked:
• helveticaneue_medium, Prime Regular are used now.

Colors

Designer to choose colors to be used in the design.

Requirements
Must have
• I would like to have a 2 sided design.
Nice to have
• I thought if we make the logo a bit bigger (without the company name), that could go to the back with the company name below. I though, if the pipe in the logo is somehow touchable on the business card, would be nice and unique.

```html
<!DOCTYPE html>
<html lang="en">
<head>
<meta charset="utf-8">
<title>Quindor and Partners – Business Card</title>
<link rel="stylesheet" href="https://fonts.googleapis.com/css2?family=Open+Sans:wght@400;600;700&display=swap">
<style>
  :root {
    --backdrop: #3b3633;
    --card: #0c0c0d;
    --card-edge: #1a1a1b;
    --brand-blue: #1ea4e2;
    --brand-magenta: #c4379c;
    --text-white: #f2f2f2;
    --silver: #a9a9ab;
  }
  * { margin: 0; padding: 0; box-sizing: border-box; }
  html, body {
    width: 1200px;
    height: 900px;
    overflow: hidden;
    background: var(--backdrop);
    font-family: "Open Sans", Arial, sans-serif;
  }
  .stage {
    position: relative;
    width: 1200px;
    height: 900px;
  }
  .card {
    position: absolute;
    top: 282px;
    width: 520px;
    height: 336px;
    background: var(--card);
    border: 1px solid var(--card-edge);
    box-shadow: 0 10px 28px rgba(0, 0, 0, 0.45);
  }
  .card--front { left: 40px; }
  .card--back { left: 640px; }

  /* brand lockup */
  .brand {
    position: absolute;
    display: flex;
    align-items: center;
    gap: 12px;
    white-space: nowrap;
  }
  .brand__square {
    width: 18px;
    height: 18px;
  }
  .brand__name {
    font-size: 30px;
    font-weight: 400;
    letter-spacing: 0.5px;
  }
  .card--front .brand { left: 118px; top: 62px; }
  .card--front .brand__square { background: var(--brand-blue); }
  .card--front .brand__name { color: var(--text-white); }
  .card--back .brand { left: 50%; top: 50%; transform: translate(-50%, -50%); }
  .card--back .brand__square { background: var(--silver); }
  .card--back .brand__name { color: var(--silver); }

  /* contact block */
  .contact {
    position: absolute;
    left: 34px;
    bottom: 34px;
    color: var(--text-white);
  }
  .contact__name {
    color: var(--brand-blue);
    font-weight: 700;
    font-size: 17px;
    letter-spacing: 0.3px;
    text-transform: uppercase;
    line-height: 1.1;
  }
  .contact__title {
    font-size: 13px;
    margin-bottom: 10px;
  }
  .contact__list { list-style: none; }
  .contact__item {
    display: flex;
    align-items: center;
    gap: 8px;
    font-size: 13px;
    line-height: 21px;
  }
  .contact__icon {
    width: 12px;
    height: 12px;
    flex: none;
    fill: var(--brand-magenta);
  }
  .contact__company {
    color: var(--brand-blue);
    font-size: 13px;
    margin-top: 4px;
    line-height: 18px;
  }
  .contact__address {
    font-size: 13px;
    line-height: 18px;
  }
</style>
</head>
<body>
<main class="stage">

  <section class="card card--front" aria-label="Business card front">
    <div class="brand">
      <span class="brand__square"></span>
      <span class="brand__name">Quindor &amp; Partners</span>
    </div>

    <div class="contact">
      <p class="contact__name">Bence Tolnavari</p>
      <p class="contact__title">Managing Director</p>
      <ul class="contact__list">
        <li class="contact__item">
          <svg class="contact__icon" viewBox="0 0 12 12" aria-hidden="true">
            <path d="M1 4c0-2 2-3 5-3s5 1 5 3l-2 1-1-2H4L3 5 1 4zM3 6h6l1 5H2l1-5zm3 1.2a1.6 1.6 0 1 0 0 3.2 1.6 1.6 0 0 0 0-3.2z"/>
          </svg>
          +36 30 518 2769
        </li>
        <li class="contact__item">
          <svg class="contact__icon" viewBox="0 0 12 12" aria-hidden="true">
            <path d="M1 2.5h10v7H1zM1.6 3l4.4 3.6L10.4 3H9.4L6 5.6 2.6 3z"/>
          </svg>
          b.tolnavari@quindor.hu
        </li>
        <li class="contact__item">
          <svg class="contact__icon" viewBox="0 0 12 12" aria-hidden="true">
            <circle cx="6" cy="6" r="5"/>
          </svg>
          www.quindor.hu
        </li>
      </ul>
      <p class="contact__company">Quindor and Partners Ltd.</p>
      <p class="contact__address">1087 Budapest, Tolvenka str. 28/C, Hungary</p>
    </div>
  </section>

  <section class="card card--back" aria-label="Business card back">
    <div class="brand">
      <span class="brand__square"></span>
      <span class="brand__name">Quindor &amp; Partners</span>
    </div>
  </section>

</main>
</body>
</html>
```